Solar and battery company needs a mailer brochure

I need a Tri-fold brochure to be mailed the size of the brochure should be 16 inches long by 8.5 inches tall high gloss finish thick paper
use a solid black background the letters should be white in color and when using borders please use red color
first page to say:
BEAT BLACKOUTS SAVE MONEY
You may qualify for a free battery system.
( include a design of the utility grid , solar panels ,battery ,money sign savings just like the PDF File show it )
at the bottom of page include Prime Volt 2 Go logo and phone number 818-555-0147
please use Knullshock fonts for the upper case letters and lower case letters as well attached is the link for the Comet Forge website for inspiration https://www.cometforgeusa.example/space-systems/solar/

Target Market(s)

residential solar clients

Industry/Entity Type

solar

Font styles to use
Other font styles liked:
• Knullshock

Colors

Designer to choose colors to be used in the design.

Requirements
Must have
• Knullshock Fonts inspired by Comet Forges website https://www.cometforgeusa.example/space-systems/solar/
Nice to have
• I would like to see a black background with white Knullshock lettering CAPITAL LETTERS and lower case letters
Should not have
• should not have solar panel images ,people get turn off if they see solar panels but they like batteries around here

```html
<!DOCTYPE html>
<html lang="en">
<head>
<meta charset="utf-8">
<title>Prime Volt 2 Go – Tri-fold Brochure</title>
<link href="https://fonts.googleapis.com/css2?family=Montserrat:wght@500;700;800;900&family=Open+Sans:wght@400;600&display=swap" rel="stylesheet">
<style>
  :root{
    --backdrop:#dcdcda;
    --paper:#000000;
    --panel-alt:#111418;
    --card:#1a1f26;
    --white:#ffffff;
    --text:#d9dde3;
    --muted:#aeb4bc;
    --red:#e02424;
    --yellow:#f5d90a;
    --ink:#000000;
    --badge:#3a3f47;
  }
  *{margin:0;padding:0;box-sizing:border-box}
  html,body{width:800px;height:1200px;overflow:hidden;background:var(--backdrop)}
  body{position:relative;font-family:"Open Sans",Arial,sans-serif;color:var(--text)}

  .spread{position:absolute;left:40px;width:720px;height:384px;display:flex;background:var(--paper);border:2px solid var(--red);box-shadow:0 6px 18px rgba(0,0,0,.18)}
  .spread--outside{top:120px}
  .spread--inside{top:680px}
  .panel{position:relative;width:240px;height:100%;overflow:hidden}
  .panel + .panel{border-left:1px solid var(--red)}

  .heading{font-family:"Montserrat",Arial,sans-serif;font-weight:800;color:var(--white);letter-spacing:.5px}
  .photo{position:absolute;border-radius:2px;border:1px solid var(--red)}

  /* outside: inner flap */
  .panel--benefits{background:var(--panel-alt);padding:26px 22px}
  .panel--benefits .heading{font-size:16px;margin-bottom:16px}
  .benefit{display:flex;gap:10px;margin-bottom:13px}
  .benefit__dot{flex:none;width:10px;height:10px;border-radius:50%;background:var(--red);margin-top:3px}
  .benefit__title{font-family:"Montserrat",Arial,sans-serif;font-weight:700;font-size:11px;color:var(--white)}
  .benefit__text{font-size:9.5px;line-height:1.35;color:var(--muted)}
  .badges{position:absolute;left:22px;bottom:22px;display:flex;gap:10px}
  .badge{width:44px;height:24px;background:var(--badge);border-radius:3px}

  /* outside: back panel */
  .panel--back{display:flex;flex-direction:column;align-items:center;justify-content:center}
  .brand-name{font-family:"Montserrat",Arial,sans-serif;font-weight:900;font-size:40px;line-height:1;color:var(--white);text-align:center;text-transform:uppercase;letter-spacing:-.5px}
  .back-contact{position:absolute;bottom:26px;left:0;right:0;text-align:center;font-size:10px;color:var(--muted)}
  .back-contact strong{display:block;font-family:"Montserrat",Arial,sans-serif;font-size:13px;color:var(--white)}

  /* outside: front cover */
  .panel--cover{padding:20px 20px}
  .cover-meta{text-align:right;font-size:8.5px;line-height:1.45;margin-bottom:12px;color:var(--muted)}
  .cover-title{font-family:"Montserrat",Arial,sans-serif;font-weight:900;font-size:20px;line-height:1.1;color:var(--white);text-transform:uppercase;margin-bottom:8px}
  .cover-offer{font-family:"Montserrat",Arial,sans-serif;font-weight:800;font-size:11px;line-height:1.5;color:var(--ink)}
  .cover-offer span{background:var(--yellow);padding:1px 4px;box-decoration-break:clone;-webkit-box-decoration-break:clone}
  .cover-art{position:absolute;left:20px;right:20px;top:192px;height:136px;border-radius:4px;border:1px solid var(--red);background:linear-gradient(135deg,#2f80d6 0%,#1d3557 65%,#0a0a0a 100%)}
  .cover-strip{position:absolute;left:0;right:0;bottom:0;height:36px;background:var(--yellow);border-top:2px solid var(--red);display:flex;align-items:center;justify-content:space-between;padding:0 18px;font-family:"Montserrat",Arial,sans-serif;font-weight:800;font-size:11px;color:var(--ink)}
  .cover-strip__brand{display:flex;align-items:center;gap:6px}
  .cover-strip__brand i{width:10px;height:10px;background:var(--ink)}

  /* inside: services */
  .panel--services{padding:26px 22px}
  .panel--services .heading{font-size:22px;margin-bottom:12px}
  .service__title{font-family:"Montserrat",Arial,sans-serif;font-weight:800;font-size:10px;color:var(--white);margin-bottom:4px}
  .service__text{font-size:9.5px;line-height:1.45;margin-bottom:14px}

  /* inside: why solar */
  .why-card{position:absolute;left:14px;right:14px;top:20px;height:190px;background:var(--card);border:1px solid var(--red);border-radius:0 40px 0 40px;padding:26px 20px}
  .why-card .heading{font-size:15px;margin-bottom:10px}
  .why-card p{font-size:9.5px;line-height:1.5}

  /* inside: gallery */
  .gallery-band{position:absolute;left:0;right:0;top:0;height:210px;background:var(--card);border-bottom:1px solid var(--red);border-left:1px solid var(--red);border-bottom-left-radius:60px}
  .gallery-caption{position:absolute;left:22px;bottom:22px;font-family:"Montserrat",Arial,sans-serif;font-weight:700;font-size:11px;color:var(--white)}
</style>
</head>
<body>

<section class="spread spread--outside">
  <article class="panel panel--benefits">
    <h2 class="heading">WHY GO SOLAR?</h2>
    <div class="benefit"><span class="benefit__dot"></span><div><div class="benefit__title">Lower Bills</div><div class="benefit__text">Cut monthly energy costs</div></div></div>
    <div class="benefit"><span class="benefit__dot"></span><div><div class="benefit__title">Backup Power</div><div class="benefit__text">Stay on during outages</div></div></div>
    <div class="benefit"><span class="benefit__dot"></span><div><div class="benefit__title">Tax Credits</div><div class="benefit__text">Save on your install</div></div></div>
    <div class="benefit"><span class="benefit__dot"></span><div><div class="benefit__title">Home Value</div><div class="benefit__text">Raise your resale price</div></div></div>
    <div class="benefit"><span class="benefit__dot"></span><div><div class="benefit__title">Clean Energy</div><div class="benefit__text">Reduce your footprint</div></div></div>
    <div class="badges"><span class="badge"></span><span class="badge"></span><span class="badge"></span></div>
  </article>

  <article class="panel panel--back">
    <h1 class="brand-name">Prime Volt<br>2 Go</h1>
    <div class="back-contact"><strong>818-555-0147</strong>Call for a free quote</div>
  </article>

  <article class="panel panel--cover">
    <div class="cover-meta">Licensed &amp; insured<br>Residential solar<br>Battery storage</div>
    <h2 class="cover-title">Beat blackouts<br>save money</h2>
    <p class="cover-offer"><span>You may qualify for</span><br><span>a free battery system.</span></p>
    <div class="cover-art" role="img" aria-label="Illustration of the utility grid, a home battery and money savings"></div>
    <div class="cover-strip">
      <span class="cover-strip__brand"><i></i>Prime Volt 2 Go</span>
      <span>818-555-0147</span>
    </div>
  </article>
</section>

<section class="spread spread--inside">
  <article class="panel panel--services">
    <h2 class="heading">SERVICES</h2>
    <h3 class="service__title">SOLAR INSTALLATION</h3>
    <p class="service__text">Our certified crews design and install rooftop systems sized to your home, handling permits, inspection and utility hookup from start to finish.</p>
    <h3 class="service__title">STORAGE BATTERIES</h3>
    <p class="service__text">Keep the lights on through outages with a home battery that stores daytime power for evenings and emergencies.</p>
    <div class="photo" style="left:22px;right:22px;bottom:22px;height:70px;background:linear-gradient(180deg,#5a6572,#1c222a)" role="img" aria-label="Photo of home battery units mounted on a garage wall"></div>
  </article>

  <article class="panel panel--why">
    <div class="why-card">
      <h2 class="heading">WHY OPT IN SOLAR</h2>
      <p>Locking in your energy costs protects your budget as utility rates keep climbing year after year.</p>
    </div>
    <div class="photo" style="left:14px;width:100px;top:228px;height:130px;background:linear-gradient(180deg,#4d79a6,#15243a)" role="img" aria-label="Photo of a residential home energy system"></div>
    <div class="photo" style="left:126px;right:14px;top:228px;height:130px;background:linear-gradient(180deg,#6b88a6,#1b2a3c)" role="img" aria-label="Photo of a technician servicing battery equipment"></div>
  </article>

  <article class="panel panel--gallery">
    <div class="gallery-band"></div>
    <div class="photo" style="left:40px;right:20px;top:26px;height:150px;background:linear-gradient(180deg,#4f7fb3,#101c2e)" role="img" aria-label="Photo of installers working on a home at sunset"></div>
    <div class="photo" style="left:20px;right:60px;top:226px;height:100px;background:linear-gradient(180deg,#6c7987,#1d242d)" role="img" aria-label="Photo of a battery storage system in a modern home"></div>
    <div class="gallery-caption">Backed by a 25-year warranty</div>
  </article>
</section>

</body>
</html>
```